Dunmore Roofing

Want a professional looking business card

Industry/Entity Type

Business

Contact Information for Business Card

Paul Dunmore ( Owner) paul@dunmoreroofing-example.com, www.dunmoreroofing-example.com, Adress: 4172 Township road 43 Ashford Creek,MB K9X4T2

```html
<!DOCTYPE html>
<html lang="en">
<head>
<meta charset="utf-8">
<title>Dunmore Roofing — Business Card</title>
<link rel="stylesheet" href="https://fonts.googleapis.com/css2?family=PT+Sans:wght@400;700&display=swap">
<style>
  :root {
    --stage: #1b1b1b;
    --card-light: #f2f2f2;
    --brand-blue: #1d4580;
    --ink: #2a2a2a;
    --white: #ffffff;
  }
  html, body {
    margin: 0;
    padding: 0;
    width: 1200px;
    height: 900px;
    overflow: hidden;
    background: var(--stage);
  }
  .canvas {
    position: relative;
    width: 1200px;
    height: 900px;
    font-family: "PT Sans", Arial, sans-serif;
  }
  .card {
    position: absolute;
    top: 170px;
    width: 347px;
    height: 561px;
    overflow: hidden;
  }
  .card--front {
    left: 259px;
    background: var(--card-light);
    text-align: center;
  }
  .card--back {
    left: 631px;
    background: var(--brand-blue);
  }
  .wordmark {
    position: absolute;
    left: 0;
    right: 0;
    top: 96px;
    margin: 0;
    color: var(--brand-blue);
    font-weight: 700;
    font-size: 38px;
    line-height: 42px;
    letter-spacing: 1px;
    text-transform: uppercase;
  }
  .contact {
    position: absolute;
    left: 0;
    right: 0;
    top: 345px;
  }
  .contact__name {
    margin: 0;
    color: var(--brand-blue);
    font-weight: 700;
    font-size: 24px;
    line-height: 28px;
    letter-spacing: 0.3px;
    text-transform: uppercase;
  }
  .contact__role {
    margin: 0;
    color: var(--ink);
    font-size: 15px;
    line-height: 18px;
  }
  .contact__rule {
    width: 147px;
    height: 1px;
    margin: 14px auto 17px;
    background: var(--brand-blue);
    border: 0;
  }
  .contact__block {
    margin: 0 0 8px;
    color: var(--ink);
    font-size: 16px;
    line-height: 20px;
    font-style: normal;
  }
  .card__bands {
    position: absolute;
    inset: 0;
  }
  .back-wordmark {
    position: absolute;
    left: 0;
    right: 0;
    top: 232px;
    margin: 0;
    text-align: center;
    color: var(--white);
    font-weight: 700;
    font-size: 42px;
    line-height: 46px;
    letter-spacing: 1px;
    text-transform: uppercase;
  }
</style>
</head>
<body>
<main class="canvas">
  <section class="card card--front" aria-label="Card front">
    <h1 class="wordmark">Dunmore<br>Roofing</h1>
    <div class="contact">
      <p class="contact__name">Paul Dunmore</p>
      <p class="contact__role">Owner</p>
      <hr class="contact__rule">
      <address class="contact__block">4172 Township road 43<br>Ashford Creek,MB K9X4T2</address>
      <p class="contact__block">paul@dunmoreroofing-example.com<br>www.dunmoreroofing-example.com</p>
    </div>
  </section>

  <section class="card card--back" aria-label="Card back">
    <svg class="card__bands" width="347" height="561" viewBox="0 0 347 561" aria-hidden="true">
      <polygon points="64,70 118,0 347,0 347,70" fill="#ffffff" opacity="0.1"/>
      <polygon points="0,0 0,55 42,0" fill="#ffffff" opacity="0.06"/>
      <polygon points="22,540 170,350 230,350 82,540" fill="#000000" opacity="0.06"/>
    </svg>
    <p class="back-wordmark">Dunmore<br>Roofing</p>
  </section>
</main>
</body>
</html>
```